Design 4 pages for an event discovery website

This is a contest for the design of 4 pages for an events discovery website. The feature is part of the new sign-up process.

Please see the attached document for a full scope, mockups and the parent category icons.

Target Market(s)

18-35 Australian event goers

Industry/Entity Type

Events

Number of Pages Required

4 page

```html
<!DOCTYPE html>
<html lang="en">
<head>
<meta charset="utf-8">
<title>Gigrova – Sign Up</title>
<link rel="stylesheet" href="https://fonts.googleapis.com/css2?family=Open+Sans:wght@400;600;700&family=Arimo:wght@700&display=swap">
<style>
  :root {
    --white: #ffffff;
    --page-bg: #f0f1f6;
    --ink: #3c3d40;
    --heading: #55575c;
    --placeholder: #a9abb0;
    --field-border: #d6d8de;
    --error: #d9534f;
    --link-blue: #5b8fc0;
    --rule: #cfd2da;
    --search-yellow: #f5c93a;
    --search-yellow-dark: #e8b22a;
    --signup-blue: #45a5c9;
    --login-green: #8aad5a;
    --cta-orange: #e08e1e;
    --footer-bg: #454545;
    --footer-text: #e6e6e6;
  }
  * { box-sizing: border-box; margin: 0; padding: 0; }
  html, body { width: 1200px; height: 584px; overflow: hidden; }
  body { font-family: "Open Sans", Arial, sans-serif; background: var(--page-bg); position: relative; }

  .site-header {
    position: absolute; left: 0; top: 0; width: 1200px; height: 133px;
    background: var(--white); box-shadow: 0 2px 3px rgba(0,0,0,.25); z-index: 2;
  }
  .brand {
    position: absolute; left: 99px; top: 49px;
    font-family: "Arimo", Arial, sans-serif; font-weight: 700; font-size: 27px;
    color: var(--ink); letter-spacing: .5px;
  }
  .search {
    position: absolute; left: 600px; top: 50px; width: 274px; height: 34px;
    background: var(--white); border: 1px solid var(--field-border); border-radius: 2px;
  }
  .search-pill {
    position: absolute; left: 9px; top: 7px; width: 254px; height: 18px;
    border-radius: 9px; border: 1px solid var(--search-yellow-dark);
    background: linear-gradient(#f8d65a, var(--search-yellow));
    color: var(--white); font-size: 11px; font-weight: 700; line-height: 16px; padding-left: 10px;
  }
  .search-pill svg { position: absolute; right: 9px; top: 3px; }
  .btn {
    position: absolute; height: 32px; color: var(--white); font-weight: 600;
    font-size: 12.5px; letter-spacing: .5px; text-align: center; line-height: 32px;
    border-radius: 2px;
  }
  .btn-signup { left: 883px; top: 50px; width: 105px; background: var(--signup-blue); }
  .btn-login { left: 996px; top: 50px; width: 105px; background: var(--login-green); }

  .page-title {
    position: absolute; left: 99px; top: 174px; font-size: 20.5px; font-weight: 400;
    color: var(--heading); letter-spacing: .3px;
  }
  .field {
    position: absolute; left: 99px; width: 268px; height: 29px;
    background: var(--white); border: 1px solid var(--field-border);
    font-size: 11.5px; color: var(--placeholder); line-height: 27px; padding-left: 8px;
  }
  .field.half { width: 130px; }
  .field.half.right { left: 236px; padding-left: 3px; }
  .field .caret {
    position: absolute; right: 8px; top: 12px; width: 0; height: 0;
    border-left: 5px solid transparent; border-right: 5px solid transparent;
    border-top: 5px solid #888;
  }
  .error {
    position: absolute; left: 378px; font-size: 11.5px; font-weight: 600; color: var(--error);
  }
  .btn-submit {
    position: absolute; left: 99px; top: 449px; width: 114px; height: 33px;
    background: var(--cta-orange); color: var(--white); font-weight: 600; font-size: 14px;
    text-align: center; line-height: 33px; border-radius: 2px; letter-spacing: .4px;
    box-shadow: 0 1px 0 #c97a12;
  }

  .benefits { position: absolute; left: 584px; top: 209px; width: 516px; list-style: none; }
  .benefits li {
    height: 34.3px; border-bottom: 1px dashed var(--rule);
    font-size: 11.3px; color: var(--link-blue); line-height: 34px; padding-left: 17px; position: relative;
  }
  .benefits li::before {
    content: ""; position: absolute; left: 1px; top: 13px;
    border-top: 4px solid transparent; border-bottom: 4px solid transparent;
    border-left: 5px solid var(--link-blue);
  }

  .site-footer {
    position: absolute; left: 0; top: 522px; width: 1200px; height: 62px; background: var(--footer-bg);
  }
  .copyright { position: absolute; left: 99px; top: 22px; font-size: 11px; color: var(--footer-text); }
  .social { position: absolute; left: 1039px; top: 22px; display: flex; gap: 10px; }
  .social span { width: 16px; height: 16px; border-radius: 50%; background: #d8d8d8; }
  .page-code { position: absolute; left: 1143px; top: 22px; font-size: 11.5px; color: var(--footer-text); }
</style>
</head>
<body>
  <header class="site-header">
    <div class="brand">GIGROVA</div>
    <div class="search">
      <div class="search-pill">Search
        <svg width="10" height="10" viewBox="0 0 10 10"><circle cx="4" cy="4" r="3" fill="none" stroke="#fff" stroke-width="1.5"/><line x1="6.2" y1="6.2" x2="9" y2="9" stroke="#fff" stroke-width="1.6"/></svg>
      </div>
    </div>
    <div class="btn btn-signup">SIGN UP</div>
    <div class="btn btn-login">LOG IN</div>
  </header>

  <main>
    <h1 class="page-title">SIGN UP</h1>
    <form>
      <div class="field" style="top:223px">User Name</div>
      <div class="field" style="top:260px">Email address</div>
      <div class="field" style="top:297px">Password</div>
      <div class="field" style="top:333px">Conform Password</div>
      <div class="field half" style="top:371px">First name<span class="caret"></span></div>
      <div class="field half right" style="top:371px">Last name<span class="caret"></span></div>
      <div class="field" style="top:408px">Date of Birth<span class="caret"></span></div>
      <div class="btn-submit">SIGN UP</div>
    </form>
    <p class="error" style="top:229px">Your User Name is Incorrect *</p>
    <p class="error" style="top:263px">Your Email id is Incorrect *</p>

    <ul class="benefits">
      <li>Get personalised event recommendations</li>
      <li>Get notified about your favourite events - never miss out again</li>
      <li>Follow all your favourite artists, musicians, teams and players in one place</li>
      <li>Follow your favourite local venues to know everything happening there</li>
      <li>Get curated news and feature content on your favourite artists</li>
      <li>Invite your mates to events via Mateshare (MS sign-up only)</li>
    </ul>
  </main>

  <footer class="site-footer">
    <p class="copyright">Copyrights@gigrova.2015.Allrights Reserved.</p>
    <div class="social" aria-label="Social links"><span></span><span></span><span></span></div>
    <p class="page-code">C11</p>
  </footer>
</body>
</html>
```